Varnik Holdings — Business Card Design Brief
Overview
Design a double-sided business card for Varnik Holdings that highlights our two service arms: Varnik Communications (telecommunications) and Varnik Energy (business energy solutions). The card should feel smart and stand out when handed to clients.

Objectives
Showcase our areas of specialty clearly.
Reflect the overall Varnik / Varnik Holdings brand while acknowledging both arms.
Explore using both logos (Communications + Energy) or one unified logo, depending on the design.

Deliverables
One double-sided business card design (front + back).

Content & Copy
Front (preferred): Logo: Varnik / Varnik Holdings
Descriptor: Business Communications | Business Energy
Back:My contact details and company details
Core products: Business Mobile • Telephony • Internet • Business Energy Solutions

Brand & Visual Direction
We have a group logo currently tailored more toward telecoms, plus a separate Varnik Energy logo.
Please explore layouts that use both logos or just one, whichever works best.
Color: I wouldn't mind seeing an option using our the Blue/Purple gradient from our website (varnik-example.co.uk), but also open to non-gradient approaches and other colours..

Overall look: Smart, modern, and distinctive.
Format & Print Specs
Double-sided business card format. (Use a standard size

Must-Haves
Front: Varnik wording or Varnik Holdings wording with atleast 1 logo also on front “Business Communications | Business Energy.”

Back: Contact + company details and core products.
A design that stands out while remaining professional.

Nice-to-Have Options
A gradient version using our site’s Blue/Purple gradient.
A non-gradient version.
A dual-logo treatment versus a single-logo treatment.

Thanks
Owen

```html
<!DOCTYPE html>
<html lang="en">
<head>
<meta charset="utf-8">
<title>Varnik Holdings – Business Card</title>
<link href="https://fonts.googleapis.com/css2?family=Poppins:wght@500;600;700&family=Montserrat:wght@400;500;600&display=swap" rel="stylesheet">
<style>
  :root{
    --stage:#d4d5d7;
    --navy:#28235a;
    --ink:#221d5c;
    --text:#1e1e2a;
    --cream:#fdfaf3;
    --white:#ffffff;
    --blue:#3a5bb8;
    --green:#3aa53c;
    --violet:#8a3b8f;
    --rule:#2a2466;
  }
  *{margin:0;padding:0;box-sizing:border-box}
  html,body{width:900px;height:1200px;overflow:hidden;background:var(--stage)}
  .canvas{position:relative;width:900px;height:1200px}
  .card{position:absolute;left:149px;width:602px;height:387px;overflow:hidden}
  .card--front{top:168px;background:var(--navy)}
  .card--back{top:644px;background:var(--cream)}

  /* front */
  .front-mark{position:absolute;left:241px;top:82px;width:120px;height:120px;border-radius:50%;background:var(--blue)}
  .front-name{position:absolute;left:0;right:0;top:214px;text-align:center;color:var(--white);
    font-family:"Poppins",sans-serif;font-weight:700;line-height:1}
  .front-name .word{display:block;font-size:60px;letter-spacing:0.5px}
  .front-name .descriptor{display:block;font-size:14px;letter-spacing:2.4px;text-transform:uppercase;margin-top:12px;white-space:nowrap}
  .front-name .sep{margin:0 8px;opacity:.8}

  /* back */
  .back-panel{position:absolute;left:22px;top:144px;right:0;bottom:0;background:var(--white)}
  .back-mark{position:absolute;left:46px;top:106px;width:120px;height:120px;border-radius:50%;background:var(--green)}
  .back-name{position:absolute;left:40px;top:238px;color:var(--ink);font-family:"Poppins",sans-serif;
    font-weight:700;font-size:60px;line-height:1}
  .divider{position:absolute;left:301px;top:106px;width:2px;height:176px;background:var(--rule)}
  .contact{position:absolute;left:321px;top:102px;font-family:"Montserrat",sans-serif;color:var(--text)}
  .contact .person{font-family:"Poppins",sans-serif;font-weight:600;font-size:26px;color:var(--ink);line-height:1.1}
  .contact .role{font-size:14px;letter-spacing:0.6px;margin-top:2px}
  .contact ul{list-style:none;margin-top:14px}
  .contact li{display:flex;align-items:center;gap:5px;font-size:15px;letter-spacing:0.8px;line-height:21px;white-space:nowrap}
  .contact li svg{width:11px;height:11px;flex:none}
  .contact address{font-style:normal;font-size:14px;line-height:23px;letter-spacing:0.3px;margin-top:14px}
  .products{position:absolute;left:34px;top:326px;font-family:"Montserrat",sans-serif;font-weight:600;
    font-size:15px;color:var(--ink);letter-spacing:0.2px;white-space:nowrap}
</style>
</head>
<body>
<main class="canvas">
  <section class="card card--front" aria-label="Card front">
    <div class="front-mark"></div>
    <h1 class="front-name"><span class="word">Varnik</span><span class="descriptor">Business Communications<span class="sep">|</span>Business Energy</span></h1>
  </section>

  <section class="card card--back" aria-label="Card back">
    <div class="back-panel"></div>
    <div class="back-mark"></div>
    <div class="back-name">Varnik</div>
    <div class="divider"></div>
    <div class="contact">
      <div class="person">Lukas Brenner</div>
      <div class="role">Geschäftsführer</div>
      <ul>
        <li><svg viewBox="0 0 24 24" fill="var(--violet)"><path d="M6.6 10.8a15 15 0 0 0 6.6 6.6l2.2-2.2c.3-.3.7-.4 1-.2 1.1.4 2.3.6 3.6.6.6 0 1 .4 1 1V20c0 .6-.4 1-1 1A17 17 0 0 1 3 4c0-.6.4-1 1-1h3.5c.6 0 1 .4 1 1 0 1.3.2 2.5.6 3.6.1.3 0 .7-.2 1z"/></svg>+44 0161 555 0148</li>
        <li><svg viewBox="0 0 24 24" fill="var(--violet)"><path d="M2 5h20v14H2z"/><path d="M2 5l10 8 10-8" stroke="#fff" stroke-width="2" fill="none"/></svg>info@varnik-example.co.uk</li>
        <li><svg viewBox="0 0 24 24" fill="none" stroke="var(--violet)" stroke-width="2"><circle cx="12" cy="12" r="10"/><path d="M2 12h20M12 2c3 3 3 17 0 20M12 2c-3 3-3 17 0 20"/></svg>varnik-example.co.uk</li>
      </ul>
      <address>24 Elmore Lane, Manchester,<br>England, M1 0ZZ</address>
    </div>
    <p class="products">Business Mobile • Telephony • Internet • Business Energy Solutions</p>
  </section>
</main>
</body>
</html>
```